Vibrant, yet professional, stationery set and other designs required.

I need to source a fantastic designer for a new project as part of my company using a new logo designed via sketch harbor.

**UPDATE** I am not looking for just 'fine' design that will suffice. I am looking for something great.

We are a life assurance brokerage based in Dublin, Ireland and BrightRoost.ie is our new website aimed at providing services for young families in Ireland. We are hoping to be the 'Velro' level of service providers in this area and I am looking for the quality of design to reflect this :-) Hopefully that makes sense!

I have a preference for straight lines over curves and waves.

I need...

1. Business card
2. Letterhead
3. Banner (for printing - 76cm X 305cm)
4. Car branding for KORVA 9 (2014 sport model) I believe the templates are freely available online.

Target Market(s)

Parents in Ireland - Aged 27 to 50.

Industry/Entity Type

Financial Planning

Colors

Designer to choose colors to be used in the design.

Requirements
Must have
• All of the items listed in the description above. I like clean, bright, legible, vibrant and professional design.
Should not have
• No silly or 'cheap' looking designs. This is a professional company looking to provide a professional service.

```html
<!DOCTYPE html>
<html lang="en">
<head>
<meta charset="utf-8">
<title>BrightRoost.ie business card</title>
<link rel="stylesheet" href="https://fonts.googleapis.com/css2?family=Open+Sans:wght@400;600;700&display=swap">
<style>
  :root {
    --backdrop: #3b322e;
    --card: #1b1c1e;
    --card-edge: #26272a;
    --ink-light: #e9e9e9;
    --ink-grey: #a9adb1;
    --accent-blue: #5fbfd6;
    --accent-green: #8dbb3f;
    --rule: #8a8d90;
  }
  * { box-sizing: border-box; margin: 0; padding: 0; }
  html, body {
    width: 1200px; height: 864px; overflow: hidden;
    background: var(--backdrop);
    font-family: "Open Sans", Arial, sans-serif;
  }
  .sheet {
    width: 1200px; height: 864px;
    display: flex; align-items: center; justify-content: center; gap: 40px;
  }
  .card {
    position: relative;
    width: 540px; height: 310px;
    background: var(--card);
    border: 1px solid var(--card-edge);
    box-shadow: 0 10px 30px rgba(0,0,0,.45);
    overflow: hidden;
  }
  /* front */
  .card--front { display: flex; align-items: center; justify-content: center; }
  .front-mark {
    display: flex; align-items: center; gap: 14px;
    font-weight: 700; font-size: 40px; letter-spacing: -0.5px;
    color: var(--ink-grey);
  }
  .front-mark .dot { width: 22px; height: 22px; border-radius: 50%; background: var(--accent-green); }
  /* back */
  .brand {
    position: absolute; right: 30px; top: 70px;
    display: flex; align-items: center; gap: 10px;
    font-weight: 700; font-size: 34px; letter-spacing: -0.5px;
    color: var(--ink-grey);
  }
  .brand .dot { width: 14px; height: 14px; border-radius: 50%; background: var(--accent-green); }
  .person { position: absolute; left: 30px; top: 96px; }
  .person__name {
    font-weight: 700; font-size: 15px; letter-spacing: .3px;
    color: var(--accent-blue); text-transform: uppercase;
  }
  .person__role {
    font-weight: 600; font-size: 14px;
    color: var(--accent-green); text-transform: uppercase;
    margin-top: 1px;
  }
  .contacts { list-style: none; margin-top: 8px; }
  .contacts li {
    display: flex; align-items: center; gap: 9px;
    font-size: 13px; line-height: 19px; color: var(--ink-light);
  }
  .contacts svg { width: 11px; height: 11px; fill: var(--ink-light); flex: none; }
  .rule-main {
    position: absolute; left: 210px; right: 0; top: 176px;
    height: 1px; background: var(--rule);
  }
  .rule-address {
    position: absolute; right: 30px; top: 226px; width: 200px;
    height: 1px; background: var(--rule);
  }
  .address {
    position: absolute; right: 30px; top: 234px;
    text-align: right; font-size: 13.5px; line-height: 19px; color: var(--ink-light);
    font-style: normal;
  }
</style>
</head>
<body>
<main class="sheet">
  <section class="card card--front" aria-label="Card front">
    <div class="front-mark"><span class="dot"></span>BrightRoost.ie</div>
  </section>

  <section class="card card--back" aria-label="Card back">
    <div class="brand"><span class="dot"></span>BrightRoost.ie</div>

    <div class="person">
      <p class="person__name">Aidan Brennan</p>
      <p class="person__role">CEO/Founder</p>
      <ul class="contacts">
        <li>
          <svg viewBox="0 0 12 12" aria-hidden="true"><path d="M1 4c0-2 2-3 5-3s5 1 5 3v1H8V4H4v1H1zM2 6h8l1 5H1z"/></svg>
          01 555 0142
        </li>
        <li>
          <svg viewBox="0 0 12 12" aria-hidden="true"><path d="M3 0h6v12H3zM4 1.5v8h4v-8z"/></svg>
          087 555 0198
        </li>
        <li>
          <svg viewBox="0 0 12 12" aria-hidden="true"><path d="M3 0h6v4H3zM0 4h12v6H9v2H3v-2H0zM4 8v3h4V8z"/></svg>
          01 555 0176
        </li>
        <li>
          <svg viewBox="0 0 12 12" aria-hidden="true"><path d="M0 2h12v1L6 7 0 3zM0 4.5l6 4 6-4V10H0z"/></svg>
          hello@brightroost.ie
        </li>
      </ul>
    </div>

    <div class="rule-main"></div>
    <div class="rule-address"></div>
    <address class="address">
      12 Harcourt Row<br>
      Dublin 2, Ireland<br>
      www.brightroost.ie
    </address>
  </section>
</main>
</body>
</html>
```